Seeking funky, innovative business cards

I am looking to refresh our current business cards to something more engaging, visual and impactful. We are a management consultancy firm, see website (www.larkstone-partners.com.au). I've included our colour scheme, sample of the slides we use and our old business cards. We would like our cards to have icons. The card should display:- Name- Title- Mobile number- Address- Email address- Website - Company logo- Our purpose statement "we build workplaces people are proud to join"

Contact Information for Business Card

Brennan Ulfsson
Consultant
0468 927 341
Level 3, 218 Wexley Street, Melbourne 3000
brennan@larkstone-partners.com.au
www.larkstone-partners.com.au

Purpose statement "we build workplaces people are proud to join"
LOGO available in google images

Font styles to use
Other font styles liked:
• Open Sans Light, Bebas Neue (open to other cool foints)

Colors
ffc214
5c5c5c
f5f5f5
fefefe

Requirements
Must have
• - Name
• - Title
• - Mobile number
• - Address
• - Email address
• - Website
• - Company logo
• - Our purpose statement "we build workplaces people are proud to join"
Nice to have
• - Icons
• - Colour (see our colour scheme"

```html
<!DOCTYPE html>
<html lang="en">
<head>
<meta charset="utf-8">
<title>Larkstone Partners – Business Card</title>
<link rel="stylesheet" href="https://fonts.googleapis.com/css2?family=Open+Sans:wght@300;400;600&display=swap">
<style>
  :root {
    --yellow: #ffc214;
    --charcoal: #474747;
    --grey: #5c5c5c;
    --light: #f5f5f5;
    --white: #fefefe;
    --tagline: #c4c4c4;
    --stage: #2b2b2b;
  }
  * { margin: 0; padding: 0; box-sizing: border-box; }
  html, body { width: 1200px; height: 880px; overflow: hidden; }
  body {
    background: var(--stage);
    font-family: "Open Sans", sans-serif;
    display: flex;
    flex-direction: column;
    align-items: center;
    justify-content: center;
    gap: 44px;
  }
  .card {
    position: relative;
    width: 600px;
    height: 340px;
    border-radius: 22px;
    overflow: hidden;
    background: var(--white);
    box-shadow: 0 10px 30px rgba(0,0,0,.35);
  }
  .brand {
    display: flex;
    align-items: center;
    gap: 10px;
    color: var(--grey);
  }
  .brand-dot {
    width: 14px; height: 14px;
    border-radius: 50%;
    background: var(--yellow);
    flex: none;
  }
  .brand-name {
    font-weight: 400;
    font-size: 40px;
    letter-spacing: -1px;
    line-height: 1;
    white-space: nowrap;
  }
  .front {
    display: flex;
    flex-direction: column;
    align-items: center;
    justify-content: center;
    gap: 20px;
  }
  .tagline {
    font-weight: 400;
    font-size: 15px;
    color: var(--tagline);
    letter-spacing: .3px;
  }
  .back-shapes { position: absolute; inset: 0; }
  .back .brand {
    position: absolute;
    left: 30px;
    top: 150px;
  }
  .back .brand-name { font-size: 32px; }
  .details {
    position: absolute;
    left: 350px;
    top: 48px;
    color: var(--white);
  }
  .person-name { font-size: 20px; font-weight: 600; line-height: 1.15; }
  .person-title { font-size: 14px; color: var(--yellow); font-weight: 400; }
  .address {
    margin-top: 22px;
    font-size: 12px;
    font-weight: 400;
    line-height: 1.45;
  }
  .contacts {
    list-style: none;
    margin-top: 18px;
    font-size: 11px;
    line-height: 1;
  }
  .contacts li {
    display: flex;
    align-items: center;
    gap: 7px;
    margin-bottom: 6px;
    white-space: nowrap;
  }
  .icon {
    width: 15px; height: 15px;
    border-radius: 50%;
    background: var(--yellow);
    flex: none;
    display: flex;
    align-items: center;
    justify-content: center;
  }
  .icon svg { width: 9px; height: 9px; }
</style>
</head>
<body>

  <section class="card front" aria-label="Card front">
    <div class="brand">
      <span class="brand-dot"></span>
      <span class="brand-name">Larkstone Partners</span>
    </div>
    <p class="tagline">we build workplaces people are proud to join</p>
  </section>

  <section class="card back" aria-label="Card back">
    <svg class="back-shapes" viewBox="0 0 600 340" preserveAspectRatio="none" aria-hidden="true">
      <path d="M182 0 Q344 95 278 340 L600 340 L600 0 Z" fill="var(--yellow)"/>
      <path d="M192 0 Q352 92 290 340 L600 340 L600 0 Z" fill="var(--white)"/>
      <path d="M200 0 Q360 90 300 340 L600 340 L600 0 Z" fill="var(--charcoal)"/>
    </svg>

    <div class="brand">
      <span class="brand-dot"></span>
      <span class="brand-name">Larkstone</span>
    </div>

    <div class="details">
      <p class="person-name">Brennan Ulfsson</p>
      <p class="person-title">Consultant</p>
      <p class="address">Level 3, 218 Wexley Street<br>Melbourne 3000<br>AUSTRALIA</p>
      <ul class="contacts">
        <li>
          <span class="icon"><svg viewBox="0 0 10 10"><path d="M2 1 L4 1 L4.6 3 L3.6 3.8 Q4.6 5.8 6.2 6.4 L7 5.4 L9 6 L9 8 Q9 9 8 9 Q1 8.5 1 2 Q1 1 2 1 Z" fill="var(--charcoal)"/></svg></span>
          0468 927 341
        </li>
        <li>
          <span class="icon"><svg viewBox="0 0 10 10"><rect x="1" y="2.5" width="8" height="5.5" fill="var(--charcoal)"/><path d="M1 2.5 L5 5.8 L9 2.5" stroke="var(--yellow)" stroke-width=".8" fill="none"/></svg></span>
          brennan@larkstone-partners.com.au
        </li>
        <li>
          <span class="icon"><svg viewBox="0 0 10 10"><circle cx="5" cy="5" r="3.8" fill="none" stroke="var(--charcoal)" stroke-width="1"/><ellipse cx="5" cy="5" rx="1.6" ry="3.8" fill="none" stroke="var(--charcoal)" stroke-width=".8"/><path d="M1.2 5 H8.8" stroke="var(--charcoal)" stroke-width=".8"/></svg></span>
          www.larkstone-partners.com.au
        </li>
        <li>
          <span class="icon"></span>
          connect.larkstone-partners.com.au
        </li>
      </ul>
    </div>
  </section>

</body>
</html>
```